13 Varno - new website design project

Our company Varno Electrical is developing a new lead generation website focused on Electrical, LED Lighting and Solar Power. We need a high converting website.

Example of our current website is www.varnoelectrical-example.com.au You can take content from this website for this new design. Our colours are red, black and white. For our new website we would like to promote Varno, Spark Every Day. Please listen to the jingle.

The below link is the company jingle that we have developed.
http://www.tunecraftdemo.com.au/vrn-tc-v1/

The key for this brief is to generate leads for Electrical, LED Lighting (for commercial) and Solar Power & Storage.

Target Market(s)

Business owners in Melbourne Victoria

Number of Pages Required

4 page

Colors
ec1f27
ffffff

Requirements
Must have
• This page must be clean, be in line with company branding and a high converting lead website.

```html
<!DOCTYPE html>
<html lang="en">
<head>
<meta charset="utf-8">
<title>Varno Electrical</title>
<link rel="stylesheet" href="https://fonts.googleapis.com/css2?family=Open+Sans:wght@400;600&family=Raleway:wght@400;500;600&display=swap">
<style>
:root{
  --red:#d7141b;
  --red-dark:#a80e13;
  --ink:#222;
  --text:#444;
  --muted:#777;
  --grey:#e6e7e8;
  --line:#cfcfcf;
  --yellow:#fff200;
  --white:#fff;
}
*{margin:0;padding:0;box-sizing:border-box}
html,body{width:1200px;height:4130px;overflow:hidden}
body{position:relative;background:var(--white);font-family:"Open Sans",Arial,sans-serif;color:var(--text)}
.abs{position:absolute}
.topline{left:0;top:0;width:1200px;height:3px;background:var(--red)}

.brand{display:flex;flex-direction:column}
.brand-row{display:flex;align-items:center;gap:12px}
.brand-dot{width:34px;height:34px;border-radius:50%;background:var(--red)}
.brand-name{font-family:"Raleway",sans-serif;font-weight:600;font-size:56px;color:var(--ink);letter-spacing:2px;line-height:1}
.brand-tag{font-family:"Raleway",sans-serif;font-weight:600;font-size:20px;color:var(--red);margin-left:46px;margin-top:6px;letter-spacing:1px}

.follow{left:718px;top:22px;font-size:10px;color:var(--ink);letter-spacing:.5px}
.social-sq{top:52px;width:20px;height:20px;border:1px solid #9bb5d6}
.phone-box{left:870px;top:0;width:202px;height:80px;border:2px solid var(--red);border-top:0;background:var(--white)}
.phone-num{left:945px;top:2px;width:127px;height:78px;background:var(--red);color:var(--white)}
.phone-num b{display:block;font-family:"Raleway",sans-serif;font-weight:600;font-size:34px;text-align:center;margin-top:6px}
.phone-num span{display:block;margin:4px auto 0;width:108px;background:#4a1a1c;font-size:12px;letter-spacing:8px;text-align:center;padding:2px 0}

.nav{left:404px;top:108px;display:flex;gap:0;font-size:11px;color:var(--ink)}
.nav a{display:block;padding:8px 10px;text-decoration:none;color:var(--ink);margin-right:20px;text-transform:uppercase}
.nav a.active{background:var(--red);color:var(--white);margin-right:8px}

.hero{left:0;top:150px;width:1200px;height:544px;background:linear-gradient(160deg,#7fb1e6 0%,#c7dcef 35%,#3e5fa8 55%,#23376f 75%,#6b5a4c 100%)}
.hero-arrow{top:240px;width:46px;height:50px;background:rgba(20,20,20,.75);display:flex;align-items:center;justify-content:center}
.hero-caption{left:656px;top:278px;width:544px;height:174px;background:rgba(40,40,40,.78);color:var(--white);padding:20px 36px}
.hero-caption h1{font-family:"Raleway",sans-serif;font-weight:500;font-size:52px;letter-spacing:1px}
.hero-caption p{font-size:19px;line-height:28px;margin-top:10px}
.dots{left:544px;top:485px;display:flex;gap:16px}
.dots i{width:10px;height:10px;border-radius:50%;background:var(--white);display:block}
.dots i+i{background:transparent;border:2px solid var(--white)}

.sec-title{left:0;width:1200px;text-align:center;font-family:"Raleway",sans-serif;font-weight:500;font-size:29px;color:var(--red)}
.sec-rule{height:2px;background:var(--red)}

.img-fill{border-radius:4px}
.svc-box{background:var(--white);border:1px solid #999;box-shadow:0 2px 6px rgba(0,0,0,.15);padding:24px 32px}
.svc-box h3{font-family:"Raleway",sans-serif;font-weight:500;font-size:19px;color:var(--ink);text-transform:uppercase}
.svc-box p{font-size:12px;line-height:22px;color:var(--text);margin-top:8px}
.btn{display:inline-block;border:1px solid var(--red);color:var(--red);font-size:10px;padding:6px 14px;margin-top:16px;text-transform:uppercase}

.about{left:0;top:1698px;width:1200px;height:434px;background:var(--grey)}
.about h2{position:absolute;left:132px;top:66px;font-family:"Raleway",sans-serif;font-weight:500;font-size:28px;color:var(--red)}
.about .rule{position:absolute;left:132px;top:116px;width:137px;height:2px;background:var(--red)}
.about p{position:absolute;left:132px;top:162px;width:533px;font-size:13px;line-height:27px;text-align:justify;color:var(--ink)}
.about .btn{position:absolute;left:131px;top:318px;margin:0}
.about .divider{position:absolute;left:733px;top:70px;width:1px;height:294px;background:#c5c5c5}

.why-col{top:2330px;width:190px;height:630px;background:linear-gradient(90deg,#ececec 0,#fff 18px)}
.why-num{font-family:"Raleway",sans-serif;font-size:48px;color:#dcdcdc;margin:10px 0 0 22px}
.why-flag{position:absolute;left:0;top:55px}
.why-col h4{position:absolute;left:42px;top:270px;width:140px;font-family:"Raleway",sans-serif;font-weight:500;font-size:17px;line-height:26px;color:var(--ink)}
.why-col p{position:absolute;left:42px;top:360px;width:140px;font-size:11px;line-height:21px;color:var(--text)}

.clients{left:0;top:3042px;width:1200px;height:676px;background:radial-gradient(ellipse at 50% 80%,#f2f2f2 0,#e4e4e4 70%)}
.client{top:195px;width:178px;height:100px;display:flex;align-items:center;justify-content:center;font-family:"Raleway",sans-serif;font-weight:600;font-size:18px;text-align:center}
.quote{left:131px;top:348px;width:937px;height:255px;background:var(--white);border-top:7px solid var(--yellow);box-shadow:0 2px 4px rgba(0,0,0,.08)}
.quote p{position:absolute;left:190px;top:68px;width:560px;text-align:center;font-size:13px;line-height:27px;color:var(--ink)}
.qmark{position:absolute;font-family:Georgia,serif;font-size:90px;color:#ddd;line-height:1}
.quote-name{position:absolute;left:348px;top:216px;width:243px;height:32px;background:var(--yellow);font-size:11px;text-align:center;line-height:32px;color:var(--ink)}
.quote-name small{font-size:8px}

.foot-h{font-size:11px;font-weight:600;color:var(--red);text-transform:uppercase}
.foot-t{font-size:10px;line-height:24px;color:var(--text)}
.foot-rule{left:0;top:4030px;width:1200px;height:1px;background:var(--line)}
.copy{left:0;top:4074px;width:1200px;text-align:center;font-size:10px;color:var(--text)}
.fsoc{width:28px;height:28px;border-radius:50%}
</style>
</head>
<body>
<div class="abs topline"></div>

<header>
  <div class="abs brand" style="left:130px;top:30px">
    <div class="brand-row"><span class="brand-dot"></span><span class="brand-name">VARNO</span></div>
    <div class="brand-tag">Spark Every Day</div>
  </div>
  <div class="abs follow">FOLLOW US</div>
  <div class="abs social-sq" style="left:720px"></div>
  <div class="abs social-sq" style="left:757px"></div>
  <div class="abs social-sq" style="left:792px;border-color:#e8a07c"></div>
  <div class="abs phone-box">
    <svg width="70" height="70" viewBox="0 0 70 70" style="margin:8px 0 0 4px" aria-hidden="true">
      <circle cx="34" cy="34" r="26" fill="none" stroke="#d7141b" stroke-width="2"/>
      <path d="M24 22c3-3 5 0 7 4 1 3-3 3-2 6 2 4 4 6 8 8 3 1 3-3 6-2 4 2 7 4 4 7-6 6-16-1-21-7-5-6-8-12-2-16z" fill="none" stroke="#d7141b" stroke-width="2.5"/>
    </svg>
  </div>
  <div class="abs phone-num"><b>139270</b><span>VARNO</span></div>
  <nav class="abs nav">
    <a class="active">Home</a><a>Varno Story</a><a>Electrical</a><a>LED Lighting</a><a>Solar Power</a><a>Our Work</a><a style="margin-right:0">Contact Us</a>
  </nav>
</header>

<section class="abs hero" role="img" aria-label="Technician installing solar panels on a tiled roof under a blue sky">
  <div class="abs hero-arrow" style="left:0"><svg width="14" height="20"><path d="M11 2 3 10l8 8" stroke="#fff" stroke-width="3" fill="none"/></svg></div>
  <div class="abs hero-arrow" style="left:1154px"><svg width="14" height="20"><path d="M3 2l8 8-8 8" stroke="#fff" stroke-width="3" fill="none"/></svg></div>
  <div class="abs hero-caption">
    <h1>SOLAR POWER</h1>
    <p>Australia's largest fully integrated Electrical<br>&amp; energy Solutions Provider</p>
  </div>
  <div class="abs dots"><i></i><i></i><i></i><i></i><i></i></div>
</section>

<h2 class="abs sec-title" style="top:750px">OUR SERVICES</h2>
<div class="abs sec-rule" style="left:507px;top:801px;width:186px"></div>

<div class="abs img-fill" style="left:280px;top:880px;width:290px;height:210px;background:radial-gradient(circle at 40% 55%,#c07a4a 0,#b33 40%,#e8c23a 60%,#fff 75%)" role="img" aria-label="Bundle of coloured electrical cables"></div>
<div class="abs svc-box" style="left:560px;top:882px;width:362px;height:146px">
  <h3>Electrical</h3><p>Great value for money, great service and reliability.</p><span class="btn">Read More</span>
</div>

<div class="abs img-fill" style="left:760px;top:1060px;width:165px;height:310px;background:radial-gradient(ellipse at 50% 30%,#f4f4f4 0,#c9c9c9 35%,#555 55%,#fff 72%)" role="img" aria-label="LED light bulb"></div>
<div class="abs svc-box" style="left:419px;top:1125px;width:362px;height:180px">
  <h3>LED Lighting</h3><p>Upgrading your business to LED Lighting is one of the quickest ways to slash the operating costs...</p><span class="btn">Read More</span>
</div>

<div class="abs img-fill" style="left:230px;top:1365px;width:360px;height:280px;background:radial-gradient(ellipse at 50% 50%,#2f63b8 0,#4a7fcf 40%,#fff 70%)" role="img" aria-label="Solar panel on a stand"></div>
<div class="abs svc-box" style="left:560px;top:1407px;width:362px;height:180px">
  <h3>Solar Power</h3><p>We have a dedicated team of solar energy consultants and installers</p><span class="btn">Read More</span>
</div>

<section class="abs about">
  <h2>ABOUT US</h2>
  <div class="rule"></div>
  <p>Varno Electrical was formed to be an expert Electricity Contracting Company providing services to all Residential and Commercial Customers. With over 10 years of experience, Varno Electrical has developed a highly-experienced team of professionals that ensure all our customer expectations are met.</p>
  <span class="btn">Read More</span>
  <div class="divider"></div>
  <div class="brand" style="position:absolute;left:800px;top:150px">
    <div class="brand-row"><span class="brand-dot"></span><span class="brand-name" style="font-size:66px">VARNO</span></div>
    <div class="brand-tag" style="font-size:23px">Spark Every Day</div>
  </div>
</section>

<h2 class="abs sec-title" style="top:2202px">WHY CHOOSE US ?</h2>
<div class="abs sec-rule" style="left:480px;top:2264px;width:243px"></div>

<div class="abs why-col" style="left:131px">
  <div class="why-num">01</div>
  <svg class="why-flag" width="152" height="175" viewBox="0 0 152 175"><path d="M0 0v175l20-20V30z" fill="#a80e13"/><path d="M20 10v150l132-75z" fill="#d7141b"/>
  <rect x="22" y="76" width="48" height="32" rx="3" fill="none" stroke="#fff" stroke-width="3"/><path d="M36 76v-7h20v7M34 84v16M58 84v16" stroke="#fff" stroke-width="3" fill="none"/></svg>
  <h4>Professional Service</h4>
  <p>When you hire a Varno Electrical Electrician you will get a professional and well-presented Electrician that comes skilled and ready to do the job.</p>
</div>
<div class="abs why-col" style="left:320px">
  <div class="why-num">02</div>
  <svg class="why-flag" width="152" height="175" viewBox="0 0 152 175"><path d="M0 0v175l20-20V30z" fill="#a80e13"/><path d="M20 10v150l132-75z" fill="#d7141b"/>
  <circle cx="44" cy="85" r="24" fill="none" stroke="#fff" stroke-width="3"/><circle cx="44" cy="85" r="14" fill="#fff"/></svg>
  <h4>5 year workmanship guarantee</h4>
  <p>You can buy with confidence as all of our work has a 5 year workmanship guarantee. For your peace of mind, we unconditionally back our electrical work. We will come back to fix any problems at our own expense.</p>
</div>
<div class="abs why-col" style="left:508px">
  <div class="why-num">03</div>
  <svg class="why-flag" width="152" height="175" viewBox="0 0 152 175"><path d="M0 0v175l20-20V30z" fill="#a80e13"/><path d="M20 10v150l132-75z" fill="#d7141b"/>
  <rect x="26" y="70" width="44" height="26" rx="3" transform="rotate(-20 48 83)" fill="none" stroke="#fff" stroke-width="3"/><circle cx="48" cy="82" r="7" fill="#fff"/><path d="M18 110l16-10" stroke="#fff" stroke-width="4"/></svg>
  <h4>Value for Money</h4>
  <p>We provide extremely competitive pricing, which means you get value for money on quality that is comparable to the best in the industry.</p>
</div>
<div class="abs why-col" style="left:698px">
  <div class="why-num">04</div>
  <svg class="why-flag" width="152" height="175" viewBox="0 0 152 175"><path d="M0 0v175l20-20V30z" fill="#a80e13"/><path d="M20 10v150l132-75z" fill="#d7141b"/>
  <circle cx="44" cy="85" r="24" fill="none" stroke="#fff" stroke-width="3"/><path d="M20 85h48M44 61v48M30 68q14 17 28 0M30 102q14-17 28 0" stroke="#fff" stroke-width="2" fill="none"/></svg>
  <h4>Environmentally friendly</h4>
  <p>We a committed to reducing carbon emissions by installing Solar Power and upgrading sites to LED Lighting. In addition to reducing the carbon emissions we recycle Fluorescent Tubes, Highbay Globes, Metal and Cardboard.</p>
</div>
<div class="abs why-col" style="left:888px">
  <div class="why-num">05</div>
  <svg class="why-flag" width="152" height="175" viewBox="0 0 152 175"><path d="M0 0v175l20-20V30z" fill="#a80e13"/><path d="M20 10v150l132-75z" fill="#d7141b"/>
  <path d="M20 86a24 22 0 0 1 48 0z" fill="none" stroke="#fff" stroke-width="3"/><path d="M44 86v18a5 5 0 0 1-10 0" stroke="#fff" stroke-width="3" fill="none"/></svg>
  <h4>Fully insured</h4>
  <p>Varno Electrical is fully insured and equipped to handle break downs and service call outs.</p>
</div>

<section class="abs clients">
  <h2 class="abs sec-title" style="top:60px;font-size:27px">Our satisfied clients include...</h2>
  <div class="abs sec-rule" style="left:420px;top:120px;width:357px"></div>
  <svg class="abs" style="left:76px;top:228px" width="16" height="30"><path d="M13 2 3 15l10 13" stroke="#999" stroke-width="2" fill="none"/></svg>
  <svg class="abs" style="left:1100px;top:228px" width="16" height="30"><path d="M3 2l10 13-10 13" stroke="#999" stroke-width="2" fill="none"/></svg>
  <div class="abs client" style="left:131px;background:var(--yellow);color:#111">Outback Supply Co</div>
  <div class="abs client" style="left:381px;background:#e3342f;color:#fff">Harbor Plumbing</div>
  <div class="abs client" style="left:638px;background:#d5161c;color:#fff">Golden Grill</div>
  <div class="abs client" style="left:888px;background:#fff;color:#2a5caa">Lakeside Retail</div>
  <svg class="abs" style="left:196px;top:336px" width="24" height="12"><path d="M0 12 12 0l12 12z" fill="#fff200"/></svg>
  <div class="abs quote">
    <span class="qmark" style="left:136px;top:30px">&ldquo;</span>
    <span class="qmark" style="left:628px;top:110px">&rdquo;</span>
    <p>The service, communication and after sales service of Varno Electrical has been awesome. We would strongly recommend them to any business contemplating upgrading their lighting or any other electrical work.</p>
    <div class="quote-name">Jordan Whitley <small>, Executive Outback Supply Co</small></div>
  </div>
</section>

<footer>
  <div class="abs brand" style="left:130px;top:3800px">
    <div class="brand-row"><span class="brand-dot"></span><span class="brand-name">VARNO</span></div>
    <div class="brand-tag">Spark Every Day</div>
  </div>
  <div class="abs foot-h" style="left:446px;top:3786px">Contact Us</div>
  <svg class="abs" style="left:446px;top:3832px" width="12" height="16"><path d="M6 15C2 9 1 7 1 5a5 5 0 0 1 10 0c0 2-1 4-5 10z" fill="#d7141b"/><circle cx="6" cy="5" r="2" fill="#fff"/></svg>
  <div class="abs foot-t" style="left:476px;top:3826px">22/48 HALDEN RD<br>GLENWICK<br>VIC 3150</div>
  <svg class="abs" style="left:446px;top:3922px" width="14" height="14"><path d="M2 2c2-2 3 0 4 2s-2 2-1 4 2 3 4 4 2-2 4-1 2 2 0 4C9 17 -1 7 2 2z" fill="#d7141b"/></svg>
  <div class="abs foot-t" style="left:476px;top:3916px">139270</div>
  <svg class="abs" style="left:446px;top:3960px" width="14" height="10"><rect width="14" height="10" fill="#d7141b"/><path d="M0 0l7 6 7-6" stroke="#fff" fill="none"/></svg>
  <div class="abs foot-t" style="left:476px;top:3952px">service@varnoelectrical-example.com.au</div>

  <div class="abs foot-h" style="left:745px;top:3780px">Quick Links</div>
  <div class="abs foot-t" style="left:746px;top:3814px">Led Lighting<br>Solar Power<br>Electrical<br>Career</div>
  <div class="abs foot-h" style="left:749px;top:3950px">Follow us :</div>
  <div class="abs fsoc" style="left:840px;top:3942px;background:#3b5bb5"></div>
  <div class="abs fsoc" style="left:875px;top:3942px;background:#1da1f2"></div>
  <div class="abs fsoc" style="left:911px;top:3942px;background:#e4573f"></div>

  <div class="abs foot-h" style="left:958px;top:3786px">Others</div>
  <div class="abs foot-t" style="left:960px;top:3818px">Terms and Conditions<br>Privacy</div>

  <div class="abs foot-rule"></div>
  <div class="abs copy">Copyrights @ 2017 All Rights Reserved</div>
</footer>
</body>
</html>
```